D-ORVIX Landing Page

We want to re-design our current home page on our website (www.pressvantiq.example) to simplify it and reduce it down to the (3) main products / services we offer. There are too many options of where they can go and it seems to be confusing for them. Additionally, we sell a higher end software product and we want the site to appear very professional for when CFO's considering our software can be confident in its quality and the long established company that we are. Our products and services are all about optimizing manufacturing production for sheet metal stampers (primarily automotive and appliance). I am including a rough power point layout of what we are thinking along with flyers for our three main products. We want to maintain the look and feel of the sample marketing materials as much as possible but does not have to match exactly. We will be producing the video ourselves to add where the power point shows a video being. Please review our website for any additional information.

deadline was too short for initial project

```html
<!DOCTYPE html>
<html lang="en">
<head>
<meta charset="utf-8">
<title>D-ORVIX Solutions</title>
<link rel="stylesheet" href="https://fonts.googleapis.com/css2?family=Roboto:wght@400;500;700&family=Roboto+Condensed:wght@700&display=swap">
<style>
  :root {
    --ink: #1e1e1e;
    --text: #444444;
    --teal: #1f4d5c;
    --yellow: #f4b818;
    --grey-bg: #f1f1f1;
    --footer: #2a2a2a;
    --white: #ffffff;
  }
  * { box-sizing: border-box; margin: 0; padding: 0; }
  html, body { width: 716px; height: 1200px; overflow: hidden; background: var(--white); }
  body { font-family: "Roboto", Arial, sans-serif; color: var(--text); position: relative; }

  .site-header { height: 62px; display: flex; align-items: center; justify-content: space-between; padding: 0 30px; }
  .brand { display: flex; align-items: center; gap: 8px; font-family: "Roboto Condensed", Arial, sans-serif; font-weight: 700; font-size: 26px; color: var(--ink); letter-spacing: 1px; }
  .brand-square { width: 26px; height: 26px; background: var(--teal); }
  .header-phone { display: flex; align-items: center; gap: 8px; font-size: 16px; font-weight: 500; color: var(--ink); }
  .phone-badge { width: 26px; height: 26px; border-radius: 50%; background: var(--yellow); display: flex; align-items: center; justify-content: center; }

  .main-nav { height: 22px; background: var(--teal); display: flex; align-items: center; gap: 20px; padding: 0 30px; }
  .main-nav a { color: var(--white); text-decoration: none; font-size: 8px; font-weight: 500; text-transform: uppercase; letter-spacing: .3px; }

  .hero { position: relative; height: 322px; }
  .hero-copy { position: absolute; left: 30px; top: 88px; width: 300px; }
  .section-title { display: flex; align-items: center; gap: 8px; font-family: "Roboto Condensed", Arial, sans-serif; font-weight: 700; font-size: 18px; color: var(--ink); text-transform: uppercase; white-space: nowrap; }
  .title-mark { width: 16px; height: 13px; background: var(--yellow); }
  .hero-copy p { margin-top: 14px; font-size: 9.5px; line-height: 1.6; }
  .btn-solid { display: inline-block; margin-top: 20px; background: var(--yellow); color: var(--ink); font-size: 8px; font-weight: 700; padding: 10px 14px; text-transform: uppercase; text-decoration: none; }
  .hero-video { position: absolute; left: 354px; top: 36px; width: 326px; height: 226px; background: linear-gradient(135deg, #3b3a36 0%, #6d5a3e 55%, #2d3b3f 100%); display: flex; align-items: center; justify-content: center; }

  .services { position: absolute; top: 406px; left: 0; width: 716px; height: 406px; background: var(--grey-bg); }
  .service { position: absolute; top: 65px; width: 182px; }
  .service:nth-child(1) { left: 65px; }
  .service:nth-child(2) { left: 270px; }
  .service:nth-child(3) { left: 471px; }
  .service-card { height: 134px; background: var(--white); box-shadow: 0 2px 8px rgba(0,0,0,.12); display: flex; align-items: center; justify-content: center; }
  .service-icon { width: 60px; height: 60px; border-radius: 8px; }
  .icon-warm { background: radial-gradient(circle, #f7cf5a, #f4b818); }
  .icon-cool { background: radial-gradient(circle, #3f6d7c, var(--teal)); }
  .service h3 { margin-top: 20px; font-family: "Roboto Condensed", Arial, sans-serif; font-size: 12.5px; font-weight: 700; color: var(--ink); line-height: 1.3; height: 34px; }
  .service p { margin-top: 6px; font-size: 7px; line-height: 1.55; height: 60px; }
  .btn-outline { display: inline-block; margin-top: 6px; border: 1.5px solid var(--yellow); color: var(--ink); font-size: 7px; font-weight: 700; padding: 8px 8px; text-transform: uppercase; text-decoration: none; }

  .guarantee { position: absolute; top: 868px; left: 0; width: 716px; text-align: center; }
  .guarantee .section-title { justify-content: center; }
  .guarantee p { margin-top: 14px; font-size: 11px; color: var(--ink); }

  .site-footer { position: absolute; top: 961px; left: 0; width: 716px; height: 239px; background: var(--footer); text-align: center; color: var(--white); }
  .site-footer .brand { justify-content: center; color: var(--white); font-size: 38px; margin-top: 38px; gap: 12px; }
  .site-footer .brand-square { width: 36px; height: 36px; background: var(--white); }
  .social-row { display: flex; justify-content: center; gap: 8px; margin-top: 18px; }
  .social-row span { width: 18px; height: 18px; border-radius: 3px; background: #5a5a5a; }
  .footer-nav { display: flex; justify-content: space-between; padding: 0 67px; margin-top: 16px; }
  .footer-nav a { color: var(--white); text-decoration: none; font-size: 7.5px; font-weight: 500; text-transform: uppercase; }
  .copyright { margin-top: 18px; font-size: 6.5px; color: #cfcfcf; }
</style>
</head>
<body>
  <header class="site-header">
    <div class="brand"><span class="brand-square"></span>D-ORVIX</div>
    <div class="header-phone">
      <span class="phone-badge">
        <svg width="14" height="14" viewBox="0 0 24 24"><path fill="#1e1e1e" d="M6.6 10.8a15.1 15.1 0 0 0 6.6 6.6l2.2-2.2a1 1 0 0 1 1-.25 11.4 11.4 0 0 0 3.6.6 1 1 0 0 1 1 1V20a1 1 0 0 1-1 1A17 17 0 0 1 3 4a1 1 0 0 1 1-1h3.5a1 1 0 0 1 1 1c0 1.25.2 2.45.57 3.57a1 1 0 0 1-.25 1z"/></svg>
      </span>
      555-014-2290
    </div>
  </header>

  <nav class="main-nav">
    <a href="#">About</a><a href="#">How we help</a><a href="#">D-ORVIX Software</a><a href="#">Transfer Simulation Service</a><a href="#">Business Case</a><a href="#">Resources</a><a href="#">Contact</a>
  </nav>

  <section class="hero">
    <div class="hero-copy">
      <h1 class="section-title"><span class="title-mark"></span>Welcome to D-ORVIX Solutions</h1>
      <p>At our core, we are a software company committed to providing cutting-edge simulation and optimization solutions. However, we understand that our customers have diverse needs and requirements which may not fit with buying software at this time. That's why we offer flexible options for you to experience the power of D-ORVIX.</p>
      <a class="btn-solid" href="#">Get Started</a>
    </div>
    <div class="hero-video" role="img" aria-label="Company video still of a stamping press line">
      <svg width="40" height="40" viewBox="0 0 40 40"><circle cx="20" cy="20" r="18" fill="none" stroke="#f4b818" stroke-width="3"/><path d="M16 12 L29 20 L16 28 Z" fill="#f4b818"/></svg>
    </div>
  </section>

  <section class="services">
    <article class="service">
      <div class="service-card"><div class="service-icon icon-warm" role="img" aria-label="Simulation screen icon"></div></div>
      <h3>New Tool Simulation and Optimization</h3>
      <p>Are you starting a new transfer tooling program soon? Trust the expertise of D-ORVIX to make it the best one you've ever had! Share your production data before you build and confidently launch your tooling at the highest possible production rates.</p>
      <a class="btn-outline" href="#">Request a Quote</a>
    </article>
    <article class="service">
      <div class="service-card"><div class="service-icon icon-cool" role="img" aria-label="Gear optimization icon"></div></div>
      <h3>Existing Tool Optimization (with or without CAD)</h3>
      <p>Are you at capacity in your transfer press, running your equipment harder than you'd like, or simply know you can be doing better? Our existing tool optimization service is a great way to increase your production efficiency (SPM) and free up press time.</p>
      <a class="btn-outline" href="#">Request a Quote</a>
    </article>
    <article class="service">
      <div class="service-card"><div class="service-icon icon-cool" role="img" aria-label="Software download icon"></div></div>
      <h3>D-ORVIX Software Products</h3>
      <p>Without question, our most successful customers are the ones who use the software themselves. D-ORVIX clients typically see as much as 40% increase in their production rates! Want to find out? Try it and see for yourself!</p>
      <a class="btn-outline" href="#">Request a Quote</a>
    </article>
  </section>

  <section class="guarantee">
    <h2 class="section-title"><span class="title-mark"></span>Our Gaurantee</h2>
    <p>You'll make your money back in your first (5) projects or we'll refund the entire purchase price!</p>
  </section>

  <footer class="site-footer">
    <div class="brand"><span class="brand-square"></span>D-ORVIX</div>
    <div class="social-row"><span></span><span></span><span></span><span></span></div>
    <nav class="footer-nav">
      <a href="#">About</a><a href="#">How we help</a><a href="#">D-ORVIX Software</a><a href="#">Transfer Simulation Service</a><a href="#">Business Case</a><a href="#">Resources</a><a href="#">Contact</a>
    </nav>
    <p class="copyright">© 2024 Copyright D-ORVIX Solutions | All Rights Reserved.</p>
  </footer>
</body>
</html>
```